Garlic Farm for Farm Sales/Restaurant sales

Need a professional, but appealing to agriculture world. We are selling 27 kinds of Organic Garlic from a farm in Simla,CO. I have uploaded logo and business information-we are going to need a template, because I will need to use it for four separate people.
-We are trying to appeal to Farm to table restaurants
-As well as growers/farmers

Target Market(s)

Agriculture Sales/Restaurants-Organic

Industry/Entity Type

Agriculture

Contact Information for Business Card

Want it to look more unique then your average kelto stock card- I want it to look amazing

Font styles to use
Sans Serif

Colors
0455a3
ec1f27
fbed22
ffffff

Requirements
Must have
• Just be creative
Nice to have
• Colorful
Should not have
• plain

```html
<!DOCTYPE html>
<html lang="en">
<head>
<meta charset="utf-8">
<title>Peak Ridge Gourmet Garlic – Business Card</title>
<link href="https://fonts.googleapis.com/css2?family=Roboto+Condensed:wght@400;700&display=swap" rel="stylesheet">
<style>
  :root {
    --navy: #16315f;
    --red: #c8223a;
    --red-soft: #e0584a;
    --yellow: #fbe122;
    --white: #ffffff;
    --page: #ecebe7;
    --ink-light: #dfe6f2;
  }
  html, body {
    margin: 0;
    padding: 0;
    width: 1200px;
    height: 950px;
    overflow: hidden;
    background: var(--page);
    font-family: "Roboto Condensed", Arial, sans-serif;
  }
  .canvas {
    position: relative;
    width: 1200px;
    height: 950px;
  }
  .card {
    position: absolute;
    left: 250px;
    width: 700px;
    height: 400px;
    border-radius: 22px;
    overflow: hidden;
    box-shadow: 0 6px 18px rgba(0,0,0,0.18);
  }
  .card-front { top: 50px; background: var(--white); }
  .card-back { top: 500px; background: var(--navy); }
  .card svg.shapes { position: absolute; inset: 0; }

  .brand {
    position: absolute;
    display: flex;
    align-items: center;
    gap: 16px;
  }
  .brand-mark {
    border-radius: 50%;
    background: var(--red);
    flex: none;
  }
  .brand-name {
    font-weight: 700;
    line-height: 1;
    letter-spacing: 0.5px;
  }
  .brand-tag {
    font-weight: 700;
    line-height: 1;
    margin-top: 4px;
  }
  .front-brand { left: 60px; top: 70px; }
  .front-brand .brand-mark { width: 70px; height: 70px; }
  .front-brand .brand-name { font-size: 44px; color: var(--navy); }
  .front-brand .brand-tag { font-size: 18px; color: var(--navy); }

  .person {
    position: absolute;
    left: 48px;
    bottom: 34px;
    color: var(--white);
  }
  .person-name {
    color: var(--yellow);
    font-weight: 700;
    font-size: 26px;
    letter-spacing: 0.5px;
  }
  .person-role, .person-email { font-size: 18px; line-height: 1.35; }

  .contact {
    position: absolute;
    right: 40px;
    top: 150px;
    color: var(--white);
    font-size: 18px;
    line-height: 1.6;
    text-align: right;
  }
  .contact-line { display: flex; justify-content: flex-end; align-items: center; gap: 8px; }
  .contact-icon { width: 16px; height: 16px; flex: none; }

  .back-mark {
    position: absolute;
    left: -70px;
    top: 40px;
    width: 320px;
    height: 320px;
    border-radius: 50%;
    background: var(--red);
    border: 10px solid var(--red-soft);
    box-sizing: border-box;
  }
  .back-brand {
    position: absolute;
    right: 60px;
    top: 150px;
    text-align: right;
  }
  .back-brand .brand-name { font-size: 56px; color: var(--white); }
  .back-brand .brand-tag { font-size: 22px; color: var(--white); margin-top: 8px; }
</style>
</head>
<body>
<main class="canvas">

  <section class="card card-front" aria-label="Business card front">
    <svg class="shapes" width="700" height="400" viewBox="0 0 700 400" aria-hidden="true">
      <path d="M0,300 C220,290 430,200 700,40 L700,400 L0,400 Z" fill="var(--navy)"/>
      <path d="M0,292 C220,282 430,192 700,32" fill="none" stroke="var(--red)" stroke-width="6"/>
      <path d="M330,220 C470,170 590,100 700,20" fill="none" stroke="var(--yellow)" stroke-width="7"/>
    </svg>

    <div class="brand front-brand">
      <span class="brand-mark"></span>
      <div>
        <div class="brand-name">Peak Ridge</div>
        <div class="brand-tag">gourmet garlic</div>
      </div>
    </div>

    <div class="contact">
      <div class="contact-line">555-014-2290
        <svg class="contact-icon" viewBox="0 0 16 16" aria-hidden="true"><path d="M3 1.5h3l1.2 3.3-1.8 1.2a8 8 0 0 0 4.6 4.6l1.2-1.8 3.3 1.2v3a1.5 1.5 0 0 1-1.6 1.5A13 13 0 0 1 1.5 3.1 1.5 1.5 0 0 1 3 1.5z" fill="var(--yellow)"/></svg>
      </div>
      <div class="contact-line">www.PeakRidgeGarlic.com</div>
      <div class="contact-line">P.O. Box 12 Larkfield, CO 80000</div>
    </div>

    <div class="person">
      <div class="person-name">DANA REED</div>
      <div class="person-role">CEO/FOUNDER</div>
      <div class="person-email">dana@PeakRidgeGarlic.com</div>
    </div>
  </section>

  <section class="card card-back" aria-label="Business card back">
    <div class="back-mark"></div>
    <div class="brand back-brand">
      <div>
        <div class="brand-name">Peak Ridge</div>
        <div class="brand-tag">gourmet garlic</div>
      </div>
    </div>
  </section>

</main>
</body>
</html>
```